Business Card Design

Looking for business card designs for a new business. there will be two cards of the same design (both lots of information below in contact info). We would like the logo diagonally across the card with the information split above and below the logo similar to sketch. happy to look at similar alternatives
Please use same colours as in logo design

Industry/Entity Type

Business

Contact Information for Business Card

Dwight Halloran
mob - 0491 738 204
ph - 02 6148 3920
fax - 02 6148 3975
email - dwight@kestrelbeams.com.au
14 Larkmoor Road, Brenthollow NSW 2391

Colin Marchetti
mob - 0438 912 557
ph - 02 6148 3920
fax - 02 6148 3975
email - colin@kestrelbeams.com.au

```html
<!DOCTYPE html>
<html lang="en">
<head>
<meta charset="utf-8">
<title>Kestrel Beams – Business Cards</title>
<link href="https://fonts.googleapis.com/css2?family=Source+Sans+3:wght@400;600;700&display=swap" rel="stylesheet">
<style>
  :root {
    --ink: #111111;
    --teal: #1a7f7a;
    --paper: #ffffff;
    --backdrop: #e9e9e7;
    --edge: #3a3a3a;
    --text: #222222;
  }
  * { margin: 0; padding: 0; box-sizing: border-box; }
  html, body {
    width: 1145px; height: 1200px; overflow: hidden;
    background: var(--backdrop);
    font-family: "Source Sans 3", Arial, sans-serif;
    color: var(--text);
  }
  .canvas { position: relative; width: 1145px; height: 1200px; }

  .card {
    position: absolute;
    background: var(--paper);
    border: 1px solid var(--edge);
    box-shadow: 0 3px 10px rgba(0,0,0,0.18);
    overflow: hidden;
  }
  .card--front { left: 158px; top: 35px; width: 940px; height: 542px; }
  .card--back  { left: 32px;  top: 620px; width: 944px; height: 540px; }

  .brand-name {
    position: absolute;
    font-weight: 700;
    color: var(--ink);
    letter-spacing: -1px;
    line-height: 1;
    display: flex; align-items: center; gap: 16px;
    white-space: nowrap;
  }
  .brand-mark { width: 0.55em; height: 0.55em; background: var(--teal); display: inline-block; }
  .card--front .brand-name { left: 32px; top: 80px; font-size: 82px; }
  .card--back .brand-name { left: 0; right: 0; top: 211px; justify-content: center; font-size: 88px; }

  .contact-list { position: absolute; left: 30px; top: 274px; list-style: none; }
  .contact-list li {
    display: flex; align-items: center; gap: 6px;
    font-size: 23px; height: 37px; color: var(--text);
  }
  .contact-icon { width: 18px; height: 18px; fill: var(--teal); flex: none; }

  .address { position: absolute; left: 30px; top: 447px; font-size: 23px; }
  .person-name {
    position: absolute; right: 14px; top: 440px;
    font-size: 31px; font-weight: 700; color: var(--teal);
  }

  .footer-band { position: absolute; left: 0; right: 0; bottom: 0; height: 26px; }
  .footer-band span { position: absolute; top: 0; height: 26px; }
  .band-ink-long  { left: 0;     width: 586px; background: var(--ink); }
  .band-teal-one  { left: 599px; width: 100px; background: var(--teal); }
  .band-ink-short { left: 721px; width: 100px; background: var(--ink); }
  .band-teal-two  { left: 837px; width: 103px; background: var(--teal); }

  .web-address {
    position: absolute; left: 0; right: 0; top: 428px;
    text-align: center; font-size: 28px; letter-spacing: 2.5px; color: var(--text);
  }
  .web-address strong { font-weight: 700; }
</style>
</head>
<body>
<main class="canvas">

  <section class="card card--front" aria-label="Business card front">
    <div class="brand-name"><span class="brand-mark"></span>Kestrel Beams</div>

    <ul class="contact-list">
      <li>
        <svg class="contact-icon" viewBox="0 0 24 24" aria-hidden="true"><path d="M6.6 10.8a15.2 15.2 0 0 0 6.6 6.6l2.2-2.2c.3-.3.7-.4 1-.2 1.1.4 2.3.6 3.6.6.6 0 1 .4 1 1V20c0 .6-.4 1-1 1A17 17 0 0 1 3 4c0-.6.4-1 1-1h3.5c.6 0 1 .4 1 1 0 1.3.2 2.5.6 3.6.1.3 0 .7-.2 1z"/></svg>
        02 6148 3920
      </li>
      <li>
        <svg class="contact-icon" viewBox="0 0 24 24" aria-hidden="true"><path d="M7 1h10a2 2 0 0 1 2 2v18a2 2 0 0 1-2 2H7a2 2 0 0 1-2-2V3a2 2 0 0 1 2-2zm0 3v13h10V4zm5 15a1.2 1.2 0 1 0 0 2.4 1.2 1.2 0 0 0 0-2.4z"/></svg>
        0438 912 557
      </li>
      <li>
        <svg class="contact-icon" viewBox="0 0 24 24" aria-hidden="true"><path d="M7 3h9l2 2v4h2a2 2 0 0 1 2 2v8h-3v2H5v-2H2v-8a2 2 0 0 1 2-2h3zm2 2v4h7V5zM7 15v4h10v-4z"/></svg>
        02 6148 3975
      </li>
      <li>
        <svg class="contact-icon" viewBox="0 0 24 24" aria-hidden="true"><path d="M2 9l10-6 10 6v11a1 1 0 0 1-1 1H3a1 1 0 0 1-1-1zm2 1.2V19h16v-8.8l-8 5z"/></svg>
        colin@kestrelbeams.com.au
      </li>
    </ul>

    <p class="address">14 Larkmoor Road, Brenthollow NSW 2391</p>
    <p class="person-name">Colin Marchetti</p>

    <div class="footer-band" aria-hidden="true">
      <span class="band-ink-long"></span>
      <span class="band-teal-one"></span>
      <span class="band-ink-short"></span>
      <span class="band-teal-two"></span>
    </div>
  </section>

  <section class="card card--back" aria-label="Business card back">
    <div class="brand-name"><span class="brand-mark"></span>Kestrel Beams</div>
    <p class="web-address">www.<strong>kestrelbeams</strong>.com.au</p>
  </section>

</main>
</body>
</html>
```